Stylish High End Wedding Videography/Films Website (BMRT)

We need a modern and high-end website look for our wedding video and films business. We films weddings all over the United Kingdom and at European destinations so need something to reflect our work. The website should be visually stunning with images and videos being the focal point as this is what our services are;

I have uploads of some items I like and the features the site needs to have. These have been taken from other websites using standout features.

We need the following pages;

1 - Homepage
2 - Films Index Page
3 - Individual Films Page
4 - Prices / Collection Page
5 - Reviews
6 - Options
7 - About
8 - Contact
9 - Blog Index
10 - Blog Page

All pages must be consistent so have a similar style.

Pages on menu:
Films
Prices
Reviews
Options
About
Contact

We require a responsive look too. Over 90% of our visitors access the website via their mobile devices.

Please use the colours from our logo to incorporate into the website.

Target Market(s)

Wedding Couples

Industry/Entity Type

Wedding Photography

Number of Pages Required

5+ page

Font styles to use
Sans Serif
Script

Requirements
Must have
• The logo must be in the centre of the menu at the top.

Social icons at the bottom of the page.

Use only two fonts including Lore which is supplied
Nice to have
• Different video for each page on the top header. This will play behind the menu.

```html
<!DOCTYPE html>
<html lang="en">
<head>
<meta charset="utf-8">
<title>BMRT Wedding Films</title>
<link href="https://fonts.googleapis.com/css2?family=Lora:wght@400;700&family=Poppins:wght@400;500;600&display=swap" rel="stylesheet">
<style>
:root{
  --gold:#a48b4b;
  --gold-dark:#8f783f;
  --ink:#1d1d1d;
  --grey:#6b6b6b;
  --line:#d9d9d9;
  --paper:#ffffff;
  --mist:#f4f4f4;
  --night:#161616;
}
*{margin:0;padding:0;box-sizing:border-box}
html,body{width:1200px;height:5272px;overflow:hidden}
body{position:relative;background:var(--paper);font-family:'Poppins',sans-serif;color:var(--ink)}
.abs{position:absolute}
.media{position:absolute;overflow:hidden}
.spaced{letter-spacing:4px;text-transform:uppercase;font-weight:600;font-size:10px}

/* hero */
.hero{left:0;top:0;width:1200px;height:966px}
.hero-photo{left:0;top:0;width:1200px;height:700px;
  background:
    radial-gradient(ellipse 180px 260px at 590px 330px,rgba(214,206,194,.55) 0%,rgba(214,206,194,0) 100%),
    radial-gradient(ellipse 260px 200px at 200px 360px,rgba(190,184,174,.35) 0%,rgba(190,184,174,0) 100%),
    radial-gradient(ellipse 420px 360px at 640px 320px,#5d564c 0%,#37332c 55%,rgba(30,30,26,0) 100%),
    linear-gradient(90deg,#1e231b 0%,#2b2e25 30%,#2a2823 60%,#20251d 100%)}
.hero-photo::after{content:"";position:absolute;inset:0;background:linear-gradient(180deg,rgba(0,0,0,.35) 0%,rgba(0,0,0,0) 22%,rgba(0,0,0,0) 70%,rgba(0,0,0,.3) 100%)}
.hero-shape{left:0;top:0}
.nav a{position:absolute;top:54px;font-family:'Lora',serif;font-size:11px;color:#fff;text-decoration:none;text-transform:uppercase;letter-spacing:.5px}
.nav a.active{color:var(--gold)}
.brand{left:500px;top:44px;width:200px;text-align:center;color:#fff}
.brand .name{font-family:'Lora',serif;font-size:18px;letter-spacing:5px}
.brand .sub{font-family:'Lora',serif;font-size:7px;letter-spacing:4px;margin-top:2px}
.nav-phone{left:1000px;top:42px;width:36px;height:36px;border-radius:50%;background:var(--gold);display:flex;align-items:center;justify-content:center}
.hero-intro{left:288px;top:690px;width:624px;text-align:center;color:#fff;font-family:'Lora',serif;font-size:17px;line-height:26.5px}
.hero-link{left:500px;top:842px;width:200px;text-align:center;color:#fff}

/* gallery */
.tile{width:300px;height:300px}
.tile-label{color:#fff;font-family:'Lora',serif;font-weight:700;font-size:14px;display:flex;align-items:center;justify-content:center}

/* intro strip */
.strip-text{left:162px;top:1626px;width:620px;font-size:11.5px;line-height:22px;color:var(--grey)}
.btn-outline{position:absolute;border:2px solid var(--gold);color:var(--gold);font-family:'Lora',serif;font-size:12px;text-transform:uppercase;display:flex;align-items:center;justify-content:center;letter-spacing:.5px}

/* testimonial */
.testimonial{left:0;top:1781px;width:1200px;height:422px;
  background:
    radial-gradient(ellipse 120px 160px at 600px 250px,rgba(150,146,138,.35) 0%,rgba(150,146,138,0) 100%),
    radial-gradient(ellipse 300px 160px at 980px 120px,rgba(90,88,84,.45) 0%,rgba(90,88,84,0) 100%),
    linear-gradient(180deg,#222220 0%,#1a1a19 55%,#121211 100%)}
.quote-mark{left:160px;top:1840px;color:#fff;font-family:'Lora',serif;font-size:72px;font-weight:700;line-height:1}
.quote-text{left:162px;top:1910px;width:660px;color:#fff;font-family:'Lora',serif;font-size:15.5px;line-height:22.5px}
.quote-thanks{left:162px;top:2004px;color:#fff;font-family:'Lora',serif;font-size:15.5px}
.quote-who{left:162px;top:2056px;color:var(--gold)}
.quote-where{left:180px;top:2076px;color:#fff;font-size:11px}

/* stories */
.section-title{width:1200px;left:0;text-align:center;font-family:'Lora',serif;font-weight:700;font-size:37px}
.stories-lede{left:250px;top:2324px;width:700px;text-align:center;font-family:'Lora',serif;font-size:17px;line-height:26.5px;color:#333}
.discover{left:0;width:1200px;top:2432px;text-align:center;color:var(--gold)}
.story{width:194px;top:2483px}
.story .thumb{width:194px;height:195px;position:relative}
.story h3{font-family:'Lora',serif;font-weight:400;font-size:11px;text-transform:uppercase;margin-top:16px}
.story p{font-size:9.5px;line-height:17px;color:var(--grey);margin-top:6px}

/* call band */
.callband{left:0;top:2842px;width:1200px;height:149px;background:var(--gold)}
.call-label{left:162px;top:2898px;font-family:'Lora',serif;font-size:24px;color:#fff}
.call-icon{left:270px;top:2893px;width:42px;height:42px;border:2px solid #fff;border-radius:50%;display:flex;align-items:center;justify-content:center}
.call-number{left:325px;top:2895px;font-family:'Lora',serif;font-size:26px;font-weight:700;color:#fff}
.call-meta{left:712px;top:2880px;width:300px;font-size:10px;line-height:17px;color:#fff;text-transform:uppercase}
.call-mail{left:712px;top:2926px;font-family:'Lora',serif;font-size:12px;font-weight:700;color:#fff;display:flex;align-items:center;gap:10px}

/* films */
.films{left:0;top:2991px;width:1200px;height:623px;background:var(--mist)}
.films-card{left:588px;top:3104px;width:450px;height:438px;background:var(--paper)}
.films-title{left:632px;top:3145px;font-family:'Lora',serif;font-weight:700;font-size:37px}
.films-sub{left:632px;top:3201px;width:380px;font-size:11px;line-height:22px;color:var(--gold);font-weight:500}
.films-copy{left:632px;top:3264px;width:360px;font-size:11.5px;line-height:22.5px;color:var(--grey)}
.films-more{left:492px;top:3516px;color:var(--gold)}

/* blog */
.post{width:270px;top:3759px;height:305px;background:var(--paper);box-shadow:0 2px 10px rgba(0,0,0,.07)}
.post .thumb{width:270px;height:176px}
.post .body{padding:16px 14px}
.post h3{font-family:'Lora',serif;font-weight:400;font-size:12px}
.post .date{font-size:9.5px;color:var(--gold);margin-top:4px}
.post p{font-size:9.5px;line-height:17px;color:var(--grey);margin-top:6px}

/* contact */
.contact{left:0;top:4140px;width:1200px;height:630px;background:var(--mist)}
.contact-card{left:162px;top:4256px;width:448px;height:438px;background:var(--paper)}
.contact-title{left:205px;top:4290px;font-family:'Lora',serif;font-weight:700;font-size:37px}
.contact-sub{left:205px;top:4338px;font-size:11px;color:var(--gold)}
.field{position:absolute;height:28px;border-bottom:1px solid var(--line);font-size:9.5px;color:var(--grey);display:flex;align-items:flex-start;justify-content:space-between}

/* footer */
.footer-photo{left:0;top:4770px;width:1200px;height:502px;
  background:
    radial-gradient(ellipse 160px 140px at 160px 110px,rgba(120,108,92,.55) 0%,rgba(120,108,92,0) 100%),
    radial-gradient(ellipse 180px 150px at 420px 120px,rgba(150,140,126,.45) 0%,rgba(150,140,126,0) 100%),
    radial-gradient(ellipse 170px 140px at 820px 100px,rgba(110,98,84,.5) 0%,rgba(110,98,84,0) 100%),
    radial-gradient(ellipse 160px 140px at 1070px 120px,rgba(140,128,112,.45) 0%,rgba(140,128,112,0) 100%),
    linear-gradient(90deg,#2a2622 0%,#3a342d 30%,#2e2a26 55%,#3d362e 80%,#221f1c 100%)}
.insta{left:469px;top:4823px;width:262px;height:60px;background:#fff;display:flex;align-items:center;justify-content:center;gap:10px;font-family:'Lora',serif;font-weight:700;font-size:13px}
.foot-brand{top:5012px}
.foot-nav a{position:absolute;top:5104px;font-family:'Lora',serif;font-size:11px;color:#fff;text-decoration:none;text-transform:uppercase}
.social{width:36px;height:36px;border:2px solid rgba(255,255,255,.85);border-radius:50%;top:5153px;display:flex;align-items:center;justify-content:center}
.social span{width:12px;height:12px;border-radius:50%;background:#fff}
.copyright{left:0;width:1200px;top:5210px;text-align:center;font-size:9px;color:#fff}
</style>
</head>
<body>

<!-- hero -->
<section class="hero abs">
  <div class="media hero-photo" role="img" aria-label="Bride and groom embracing beneath trees on their wedding day"></div>
  <svg class="abs hero-shape" width="1200" height="966" aria-hidden="true"><polygon points="0,672 600,582 1200,672 1200,966 0,966" fill="var(--gold)"/></svg>
  <nav class="nav">
    <a class="active" style="left:163px">Home</a>
    <a style="left:242px">Films</a>
    <a style="left:320px">Prices</a>
    <a style="left:401px">Reviews</a>
    <a style="left:731px">Options</a>
    <a style="left:827px">About</a>
    <a style="left:909px">Contact</a>
  </nav>
  <div class="abs brand"><div class="name">BMRT</div><div class="sub">WEDDING FILMS</div></div>
  <div class="abs nav-phone"><svg width="16" height="16" viewBox="0 0 24 24"><path d="M6.6 10.8a15.1 15.1 0 0 0 6.6 6.6l2.2-2.2a1 1 0 0 1 1-.25 11.4 11.4 0 0 0 3.6.57 1 1 0 0 1 1 1V20a1 1 0 0 1-1 1A17 17 0 0 1 3 4a1 1 0 0 1 1-1h3.5a1 1 0 0 1 1 1c0 1.25.2 2.45.57 3.57a1 1 0 0 1-.25 1z" fill="#fff"/></svg></div>
  <p class="abs hero-intro">BMRT is a wedding filmmaker based in the North East of England. We film weddings in a fun and natural way. All weddings are totally unique to the couple. If you are looking for a wedding film for your special day we'd love to hear from you.</p>
  <div class="abs hero-link spaced">About us</div>
</section>

<!-- gallery -->
<div class="media tile" style="left:0;top:966px;background:radial-gradient(ellipse 130px 150px at 150px 190px,#f2efe8 0%,rgba(242,239,232,0) 100%),radial-gradient(ellipse 110px 110px at 170px 90px,#d8b9a0 0%,rgba(216,185,160,0) 100%),linear-gradient(135deg,#c9c3b4,#8e8a78)" role="img" aria-label="Bride holding a white bouquet"></div>
<div class="media tile tile-label" style="left:300px;top:966px;background:radial-gradient(ellipse 120px 170px at 170px 200px,#6b6561 0%,rgba(107,101,97,0) 100%),radial-gradient(ellipse 90px 120px at 130px 120px,#4a2f33 0%,rgba(74,47,51,0) 100%),linear-gradient(135deg,#2b2523,#141211)" role="img" aria-label="Couple kissing in a dim hall">Hart &amp; Maya</div>
<div class="media tile" style="left:600px;top:966px;background:radial-gradient(ellipse 110px 140px at 140px 170px,#d9d4cd 0%,rgba(217,212,205,0) 100%),linear-gradient(180deg,#55504a,#3a3632 60%,#2b2825)" role="img" aria-label="Bride celebrating with bridesmaids"></div>
<div class="media tile" style="left:900px;top:966px;background:radial-gradient(circle 90px at 120px 130px,#c2263f 0%,rgba(194,38,63,0) 100%),radial-gradient(circle 80px at 200px 190px,#e37c8f 0%,rgba(227,124,143,0) 100%),linear-gradient(135deg,#f1eeea,#dcd5cf)" role="img" aria-label="Red and pink rose bouquet"></div>
<div class="media tile" style="left:0;top:1266px;background:radial-gradient(ellipse 80px 140px at 130px 200px,#d9d5cc 0%,rgba(217,213,204,0) 100%),radial-gradient(ellipse 60px 120px at 80px 180px,#2b3244 0%,rgba(43,50,68,0) 100%),linear-gradient(180deg,#3f4a36,#2a3323 70%,#4a5540)" role="img" aria-label="Couple hugging in a forest"></div>
<div class="media tile" style="left:300px;top:1266px;background:radial-gradient(ellipse 90px 150px at 150px 200px,#e7e2d8 0%,rgba(231,226,216,0) 100%),radial-gradient(ellipse 200px 120px at 150px 60px,#b58f4f 0%,rgba(181,143,79,0) 100%),linear-gradient(180deg,#4a4328,#2f2c1c 60%,#5b5639)" role="img" aria-label="Bride walking on a woodland path"></div>
<div class="media tile" style="left:600px;top:1266px;background:radial-gradient(ellipse 70px 140px at 100px 200px,#ece8df 0%,rgba(236,232,223,0) 100%),radial-gradient(ellipse 70px 150px at 190px 190px,#3b3d42 0%,rgba(59,61,66,0) 100%),linear-gradient(180deg,#7f8569,#9a9c82 60%,#6d6f5c)" role="img" aria-label="Couple walking hand in hand"></div>
<div class="media tile" style="left:900px;top:1266px;background:radial-gradient(ellipse 140px 150px at 150px 210px,#f1ede8 0%,rgba(241,237,232,0) 100%),radial-gradient(ellipse 160px 90px at 120px 40px,#d6c341 0%,rgba(214,195,65,0) 100%),linear-gradient(180deg,#b9ad48,#8d9b62 50%,#c8c2b6)" role="img" aria-label="Two brides among yellow flowers"></div>

<!-- intro strip -->
<p class="abs strip-text">Lorem Ipsum is simply dummy text of the printing and typesetting industry. Lorem Ipsum has been the industry's standard dummy text ever since the 1500s, when an unknown printer took a galley of type and scrambled it to make a type specimen book.</p>
<div class="btn-outline" style="left:884px;top:1641px;width:155px;height:46px">Wedding Films</div>

<!-- testimonial -->
<section class="abs testimonial" role="img" aria-label="Couple silhouetted on a beach at dusk"></section>
<div class="abs quote-mark">&ldquo;</div>
<p class="abs quote-text">One of the best decisions We made was choosing you guys to film our wedding! It's absolutely fantastic, it has everyone so emotional watching it, we can't thank you enough for capturing our special day! You were amazing from start to finish</p>
<p class="abs quote-thanks">Thanks so much.</p>
<div class="abs quote-who spaced">&ndash; Laura and James</div>
<div class="abs quote-where">Oakmere Hall</div>

<!-- stories -->
<h2 class="abs section-title" style="top:2268px">Stories</h2>
<p class="abs stories-lede">Your wedding day is a once in a lifetime moment. A moment in time where all the people you love and care about are in the same place at the same time. We document unique moments on film. The laughs, the tears and the love.</p>
<div class="abs discover spaced">Discover more</div>

<article class="abs story" style="left:162px">
  <div class="thumb" style="background:radial-gradient(ellipse 80px 110px at 60px 90px,#d9d6d2 0%,rgba(217,214,210,0) 100%),linear-gradient(135deg,#b7b2ac,#4a4744 70%,#252322)" role="img" aria-label="Bride in veil with groom behind"></div>
  <h3>Cinematic Highlights Film</h3>
  <p>A highlights film, a harmony of moving imagery, vocals and music, which is unique to you.</p>
</article>
<article class="abs story" style="left:389px">
  <div class="thumb" style="background:radial-gradient(ellipse 90px 100px at 97px 110px,#8a8784 0%,rgba(138,135,132,0) 100%),linear-gradient(180deg,#4a4846,#232222)" role="img" aria-label="Black and white ceremony scene">
    <svg class="abs" style="left:77px;top:78px" width="40" height="40" viewBox="0 0 40 40"><circle cx="20" cy="20" r="18" fill="none" stroke="#fff" stroke-width="2"/><polygon points="16,12 29,20 16,28" fill="#fff"/></svg>
  </div>
  <h3>Ceremony and Speeches</h3>
  <p>Want to hear the moment you say your vows or I Do or even see your first kiss?</p>
</article>
<article class="abs story" style="left:616px">
  <div class="thumb" style="background:radial-gradient(ellipse 90px 100px at 90px 90px,#d3ad8e 0%,rgba(211,173,142,0) 100%),linear-gradient(135deg,#9b8a6e,#5f7844 70%,#3f5a2c)" role="img" aria-label="Smiling bride close up"></div>
  <h3>Extended Documentary Film</h3>
  <p>The whole story of your wedding from the morning preparations through to just after the first...</p>
</article>
<article class="abs story" style="left:843px">
  <div class="thumb" style="background:radial-gradient(ellipse 70px 120px at 140px 110px,#eeece8 0%,rgba(238,236,232,0) 100%),linear-gradient(90deg,#233049,#2d3a55 50%,#cfd0d4)" role="img" aria-label="Groom and bride embracing"></div>
  <h3>Our Story Feature</h3>
  <p>Every wedding has a unique story behind how both of you met. Our Love Story extra is a perfect...</p>
</article>

<!-- call band -->
<section class="abs callband"></section>
<div class="abs call-label">CALL US</div>
<div class="abs call-icon"><svg width="20" height="20" viewBox="0 0 24 24"><path d="M6.6 10.8a15.1 15.1 0 0 0 6.6 6.6l2.2-2.2a1 1 0 0 1 1-.25 11.4 11.4 0 0 0 3.6.57 1 1 0 0 1 1 1V20a1 1 0 0 1-1 1A17 17 0 0 1 3 4a1 1 0 0 1 1-1h3.5a1 1 0 0 1 1 1c0 1.25.2 2.45.57 3.57a1 1 0 0 1-.25 1z" fill="none" stroke="#fff" stroke-width="1.6"/></svg></div>
<div class="abs call-number">07000 318 252</div>
<div class="abs call-meta">Wedding videography &bull; North East, UK and worldwide films</div>
<div class="abs call-mail"><svg width="16" height="12" viewBox="0 0 16 12"><rect x="0" y="0" width="16" height="12" rx="1" fill="#fff"/><polyline points="1,1 8,7 15,1" fill="none" stroke="var(--gold)" stroke-width="1.4"/></svg>hello@bmrtfilms.example</div>

<!-- films -->
<section class="abs films"></section>
<div class="media" style="left:162px;top:3066px;width:448px;height:440px;background:radial-gradient(ellipse 110px 180px at 320px 260px,#ece9e3 0%,rgba(236,233,227,0) 100%),radial-gradient(ellipse 110px 190px at 150px 280px,#243049 0%,rgba(36,48,73,0) 100%),linear-gradient(180deg,#c2a56c,#8c7446 45%,#6f5f45)" role="img" aria-label="Groom kissing bride's cheek indoors"></div>
<div class="abs films-card"></div>
<h2 class="abs films-title">Films</h2>
<p class="abs films-sub">I'd love to hear from you if you are getting married.<br>Please fill in the form below to check my availability.</p>
<p class="abs films-copy">Lorem Ipsum is simply dummy text of the printing and typesetting industry. Lorem Ipsum has been the industry's standard dummy text ever since the 1500s, when an unknown printer took a galley of type and scrambled it to make a type specimen book.</p>
<div class="btn-outline" style="left:632px;top:3416px;width:172px;height:44px">Wedding Videos</div>
<div class="abs films-more spaced">+ Prices</div>

<!-- blog -->
<h2 class="abs section-title" style="top:3682px">Latest Blog</h2>
<article class="abs post" style="left:162px">
  <div class="thumb" style="background:radial-gradient(ellipse 110px 70px at 140px 100px,#e3a6ae 0%,rgba(227,166,174,0) 100%),linear-gradient(180deg,#6d7c45,#8a8a5a 50%,#c9a3a0)" role="img" aria-label="Wedding rings resting on a flower"></div>
  <div class="body"><h3>Lorem Ipsum is simply dummy text</h3><div class="date">27 July 2020</div><p>Lorem Ipsum is simply dummy text of the printing and typesetting industry. Lorem Ipsum has been the industry's standard dummy...</p></div>
</article>
<article class="abs post" style="left:465px">
  <div class="thumb" style="background:radial-gradient(ellipse 120px 70px at 140px 120px,#d7cfc6 0%,rgba(215,207,198,0) 100%),linear-gradient(90deg,#2a2826,#4b4843 50%,#a9c2bf)" role="img" aria-label="Bridesmaids laughing together"></div>
  <div class="body"><h3>Lorem Ipsum is simply dummy text</h3><div class="date">27 July 2020</div><p>Lorem Ipsum is simply dummy text of the printing and typesetting industry. Lorem Ipsum has been the industry's standard dummy...</p></div>
</article>
<article class="abs post" style="left:768px">
  <div class="thumb" style="background:radial-gradient(ellipse 90px 70px at 180px 130px,#f3f1ee 0%,rgba(243,241,238,0) 100%),linear-gradient(180deg,#9fb3cc,#8d9db0 45%,#b9a58a)" role="img" aria-label="Bride on stone steps by the sea"></div>
  <div class="body"><h3>Lorem Ipsum is simply dummy text</h3><div class="date">27 July 2020</div><p>Lorem Ipsum is simply dummy text of the printing and typesetting industry. Lorem Ipsum has been the industry's standard dummy...</p></div>
</article>

<!-- contact -->
<section class="abs contact"></section>
<div class="media" style="left:588px;top:4219px;width:450px;height:438px;background:radial-gradient(ellipse 100px 200px at 170px 270px,#efebe2 0%,rgba(239,235,226,0) 100%),radial-gradient(ellipse 90px 200px at 320px 270px,#3b4150 0%,rgba(59,65,80,0) 100%),linear-gradient(135deg,#6f8a4a,#a3ad7d 50%,#5c7340)" role="img" aria-label="Couple walking arm in arm in a garden"></div>
<div class="abs contact-card"></div>
<h2 class="abs contact-title">Contact Us</h2>
<div class="abs contact-sub">I'd love to chat more about your wedding...</div>
<div class="field" style="left:205px;top:4385px;width:176px">First Name</div>
<div class="field" style="left:392px;top:4385px;width:173px">Surname</div>
<div class="field" style="left:205px;top:4430px;width:176px">What your partner's name?</div>
<div class="field" style="left:392px;top:4430px;width:173px">Email Address</div>
<div class="field" style="left:205px;top:4475px;width:176px">Mobile No.</div>
<div class="field" style="left:392px;top:4475px;width:173px">Select Date<svg width="14" height="12" viewBox="0 0 14 12"><rect x="1" y="1.5" width="12" height="10" fill="none" stroke="#999"/><line x1="1" y1="4.5" x2="13" y2="4.5" stroke="#999"/></svg></div>
<div class="field" style="left:205px;top:4520px;width:360px;height:50px">I'd love to know how you met. Tell me your story...</div>
<div class="btn-outline" style="left:205px;top:4587px;width:173px;height:45px">Send Story</div>

<!-- footer -->
<div class="media footer-photo" role="img" aria-label="Montage of wedding guests and couples"></div>
<div class="abs insta"><svg width="14" height="14" aria-hidden="true"><rect x="1" y="1" width="12" height="12" fill="none" stroke="var(--ink)" stroke-width="1.6"/></svg>BMRTFILMS</div>
<svg class="abs" style="left:0;top:4900px" width="1200" height="372" aria-hidden="true"><polygon points="0,168 600,46 1200,168 1200,372 0,372" fill="var(--gold)"/></svg>
<div class="abs brand foot-brand"><div class="name">BMRT</div><div class="sub">WEDDING FILMS</div></div>
<nav class="foot-nav">
  <a style="left:308px">Home</a>
  <a style="left:386px">Films</a>
  <a style="left:464px">Prices</a>
  <a style="left:547px">Reviews</a>
  <a style="left:641px">Options</a>
  <a style="left:738px">About</a>
  <a style="left:821px">Contact</a>
</nav>
<div class="abs social" style="left:529px" aria-label="Social link"><span></span></div>
<div class="abs social" style="left:582px" aria-label="Social link"><span></span></div>
<div class="abs social" style="left:635px" aria-label="Social link"><span></span></div>
<div class="abs copyright">&copy; BMRT &ndash; 2020. All Rights Reserved.</div>

</body>
</html>
```